Gobal construction supply company needs new business card design

I need a business card design for my global supply company using an existing logo. i will be looking to print these on rounded corner cards with the black background version of my logo on the back. on the front white background, my logo again and my simple details.

```html
<!DOCTYPE html>
<html lang="en">
<head>
<meta charset="utf-8">
<title>Kestrel Build Supply – Business Card</title>
<link rel="stylesheet" href="https://fonts.googleapis.com/css2?family=Montserrat:wght@600&family=Arimo:wght@400;700&display=swap">
<style>
  :root {
    --backdrop: #3a3a3a;
    --card-white: #f1f1f1;
    --brand-red: #d50000;
    --ink: #111111;
    --ink-soft: #444444;
    --card-dark: #1d1d1d;
    --bar-dark: #1a1a1a;
    --white: #ffffff;
  }
  html, body {
    margin: 0;
    width: 1200px;
    height: 960px;
    overflow: hidden;
    background: var(--backdrop);
  }
  .canvas { position: relative; width: 1200px; height: 960px; }

  .card {
    position: absolute;
    width: 600px;
    height: 344px;
    border-radius: 22px;
    overflow: hidden;
  }

  /* Front */
  .card-front { left: 186px; top: 112px; background: var(--card-white); }
  .front-art { position: absolute; left: 0; top: 0; }
  .company-name {
    position: absolute; left: 29px; top: 38px; margin: 0;
    font: 600 22px/1 "Montserrat", sans-serif;
    color: var(--ink); letter-spacing: 0.2px;
  }
  .detail-icon { position: absolute; left: 29px; width: 28px; height: 28px; }
  .person-name {
    position: absolute; left: 73px; top: 108px; margin: 0;
    font: 700 22px/1 "Arimo", sans-serif; color: var(--ink);
  }
  .person-role {
    position: absolute; left: 73px; top: 132px; margin: 0;
    font: 700 15px/1 "Arimo", sans-serif; color: var(--brand-red);
  }
  .contact-lines {
    position: absolute; left: 73px; margin: 0;
    font: 400 14px/18px "Arimo", sans-serif; color: var(--ink-soft);
  }
  .panel-mark {
    position: absolute; left: 384px; top: 166px; width: 200px; margin: 0;
    font: 600 24px/1.15 "Montserrat", sans-serif; color: var(--white);
    text-align: center;
  }
  .address-bar {
    position: absolute; left: 0; bottom: 0; width: 100%; height: 48px;
    background: var(--bar-dark);
  }
  .address-text {
    position: absolute; left: 73px; top: 15px; margin: 0;
    font: 400 14px/18px "Arimo", sans-serif; color: var(--white);
  }
  .address-bar .detail-icon { top: 10px; }

  /* Back */
  .card-back {
    left: 434px; top: 512px; height: 342px; background: var(--card-dark);
    display: flex; align-items: center; justify-content: center;
  }
  .back-mark-name {
    margin: 0; font: 600 24px/1 "Montserrat", sans-serif; color: var(--white);
  }
</style>
</head>
<body>
<main class="canvas">

  <section class="card card-front" aria-label="Business card front">
    <svg class="front-art" width="600" height="344" viewBox="0 0 600 344" aria-hidden="true">
      <polygon points="474,0 600,0 600,296 286,296" fill="var(--brand-red)"/>
    </svg>

    <h1 class="company-name">KESTREL BUILD SUPPLY</h1>

    <svg class="detail-icon" style="top:116px" viewBox="0 0 28 28" aria-hidden="true">
      <circle cx="14" cy="14" r="13" fill="var(--brand-red)"/>
      <circle cx="14" cy="11" r="4" fill="#fff"/>
      <path d="M7 21c1-4 4-5.5 7-5.5s6 1.5 7 5.5z" fill="#fff"/>
    </svg>
    <p class="person-name">DANIEL HARPER</p>
    <p class="person-role">CEO/FOUNDER</p>

    <svg class="detail-icon" style="top:180px" viewBox="0 0 28 28" aria-hidden="true">
      <circle cx="14" cy="14" r="13" fill="var(--brand-red)"/>
      <rect x="10" y="7" width="8" height="14" rx="1.5" fill="none" stroke="#fff" stroke-width="1.6"/>
      <circle cx="14" cy="18.5" r="0.9" fill="#fff"/>
    </svg>
    <p class="contact-lines" style="top:177px">555.214.7730<br>555.318.4092</p>

    <svg class="detail-icon" style="top:240px" viewBox="0 0 28 28" aria-hidden="true">
      <circle cx="14" cy="14" r="13" fill="var(--brand-red)"/>
      <rect x="8" y="9.5" width="12" height="9" fill="#fff"/>
      <path d="M8 9.5l6 5 6-5" fill="none" stroke="var(--brand-red)" stroke-width="1.2"/>
    </svg>
    <p class="contact-lines" style="top:231px">daniel@kestrelbuild.com<br>www.kestrelbuild.com</p>

    <p class="panel-mark">KESTREL<br>BUILD<br>SUPPLY</p>

    <div class="address-bar">
      <svg class="detail-icon" viewBox="0 0 28 28" aria-hidden="true">
        <circle cx="14" cy="14" r="13" fill="var(--brand-red)"/>
        <path d="M14 21s-5-5.5-5-9a5 5 0 0 1 10 0c0 3.5-5 9-5 9z" fill="#fff"/>
        <circle cx="14" cy="12" r="1.8" fill="var(--brand-red)"/>
      </svg>
      <p class="address-text">1420 Harbor Street, Portside, Westland 20418</p>
    </div>
  </section>

  <section class="card card-back" aria-label="Business card back">
    <p class="back-mark-name">KESTREL BUILD SUPPLY</p>
  </section>

</main>
</body>
</html>
```